design a construction company business card

Design business card around our logo. Card must have all the typical info: name, title, address, phone, email, business name, etc. Somewhere on the card I would like to see our motto "Built on integrity... Inspired by commitment." Consider adding a splash of bright orange to the card to complement the blues and silvers/grays in the logo. We are open to metallic inks, textures, etc. We would like to see options on both light and dark backgrounds. The font in the logo is Euro Technic Extended Regular.

```html
<!DOCTYPE html>
<html lang="en">
<head>
<meta charset="utf-8">
<title>Harlow Contracting – Business Card</title>
<link rel="stylesheet" href="https://fonts.googleapis.com/css2?family=Exo+2:ital,wght@0,400;0,500;0,700;1,700;1,800&family=Michroma&display=swap">
<style>
  :root {
    --stage: #8a6a45;
    --brand-blue: #1f5fc0;
    --brand-blue-deep: #1d3fa6;
    --brand-blue-light: #2a74d0;
    --steel: #a9a49c;
    --steel-dark: #8f8a82;
    --ink: #000000;
    --paper: #ffffff;
  }
  * { box-sizing: border-box; margin: 0; padding: 0; }
  html, body {
    width: 1189px; height: 1200px; overflow: hidden;
    background: var(--stage);
  }
  .stage { position: relative; width: 1189px; height: 1200px; }

  .card {
    position: absolute; top: 202px; width: 437px; height: 765px;
    border-radius: 24px; overflow: hidden;
    background: var(--paper);
    box-shadow: 0 6px 14px rgba(0,0,0,0.35);
    font-family: "Exo 2", sans-serif;
    color: var(--paper);
  }
  .card--front { left: 141px; }
  .card--back { left: 597px; }

  .band { position: absolute; left: 0; width: 100%; }
  .band--top { top: 0; height: 29px; background: linear-gradient(var(--brand-blue-deep), var(--brand-blue)); }
  .band--steel-upper { top: 318px; height: 29px; background: linear-gradient(var(--steel), var(--steel-dark)); }
  .band--mid { top: 347px; height: 47px; background: linear-gradient(var(--brand-blue-light), var(--brand-blue-deep)); }
  .band--steel-lower { top: 394px; height: 29px; background: linear-gradient(var(--steel-dark), var(--steel)); }
  .panel { top: 423px; height: 285px; background: var(--ink); }
  .band--rule { top: 708px; height: 6px; background: var(--paper); }
  .band--footer {
    top: 714px; height: 51px;
    background: linear-gradient(var(--brand-blue-light), var(--brand-blue-deep));
    display: flex; align-items: center; justify-content: center;
    font-size: 19px; letter-spacing: 1.5px; font-weight: 500;
  }

  .brand {
    position: absolute; top: 118px; left: 0; width: 100%;
    display: flex; flex-direction: column; align-items: center; gap: 8px;
    color: var(--brand-blue-deep);
    font-family: "Exo 2", sans-serif; font-weight: 700;
  }
  .brand__mark { width: 16px; height: 16px; background: var(--brand-blue-deep); }
  .brand__name { font-size: 54px; letter-spacing: 6px; line-height: 1; }
  .brand__sub { font-size: 18px; letter-spacing: 2px; line-height: 1; }

  .motto {
    position: absolute; top: 423px; left: 0; width: 100%; height: 285px;
    display: flex; align-items: center; justify-content: center;
    text-align: center; font-style: italic; font-weight: 800;
    font-size: 29px; line-height: 1.32; letter-spacing: 0.5px;
  }

  .contact {
    position: absolute; top: 443px; left: 0; width: 100%;
    text-align: center;
  }
  .contact__name { font-family: "Michroma", sans-serif; font-size: 25px; letter-spacing: 1px; line-height: 1.2; }
  .contact__title { color: var(--brand-blue-light); font-size: 21px; margin-top: 2px; }
  .contact__address { font-size: 19px; line-height: 1.33; margin-top: 10px; letter-spacing: 0.5px; }
  .contact__label { color: var(--brand-blue-light); font-style: italic; font-weight: 700; font-size: 18px; margin-top: 10px; }
  .contact__value { font-size: 20px; letter-spacing: 0.5px; }
  .contact__divider {
    width: 250px; height: 2px; margin: 8px auto 0;
    background: linear-gradient(90deg, transparent, var(--brand-blue-light), transparent);
  }
</style>
</head>
<body>
<main class="stage">
  <section class="card card--front">
    <div class="band band--top"></div>
    <div class="brand">
      <span class="brand__mark"></span>
      <span class="brand__name">HARLOW</span>
      <span class="brand__sub">CONTRACTING, INC.</span>
    </div>
    <div class="band band--steel-upper"></div>
    <div class="band band--mid"></div>
    <div class="band band--steel-lower"></div>
    <div class="band panel"></div>
    <p class="motto">Built on integrity...<br>Inspired by<br>commitment.</p>
    <div class="band band--rule"></div>
    <div class="band band--footer">www.HARLOWBUILD.com</div>
  </section>

  <section class="card card--back">
    <div class="band band--top"></div>
    <div class="brand">
      <span class="brand__mark"></span>
      <span class="brand__name">HARLOW</span>
      <span class="brand__sub">CONTRACTING, INC.</span>
    </div>
    <div class="band band--steel-upper"></div>
    <div class="band band--mid"></div>
    <div class="band band--steel-lower"></div>
    <div class="band panel"></div>
    <div class="contact">
      <h1 class="contact__name">DANIEL REEVE</h1>
      <p class="contact__title">Founder</p>
      <p class="contact__address">PO BOX 456 your address<br>5th street Ashford</p>
      <p class="contact__label">Phone:</p>
      <p class="contact__value">(555) 214-7390</p>
      <div class="contact__divider"></div>
      <p class="contact__label">Email:</p>
      <p class="contact__value">info@harlowbuild.com</p>
    </div>
    <div class="band band--rule"></div>
    <div class="band band--footer">www.HARLOWBUILD.com</div>
  </section>
</main>
</body>
</html>
```